KBT Business Cards

We require business cards for our business. We would like a matte black back to the card, with our logo centred in the middle. The front side of the card is open to design.

Target Market(s)

Clients looking for legal services (professional)

Industry/Entity Type

Legal

Contact Information for Business Card

Doran Kelbrath
Partner
Mobile: 0461 738 524
Email: doran@kbtlaw.co
Website: www.kbtlaw.co
Level 3, 118 Wendmore Street
Sydney NSW 2000

Font styles to use
Other font styles liked:
• Avenir

Colors
f04a50
ffffff
1b1b1b

Requirements
Must have
• Black back with logo included in the centre of the card.
• Our font is Avenir.

```html
<!DOCTYPE html>
<html lang="en">
<head>
<meta charset="utf-8">
<title>KBT Business Cards</title>
<link rel="stylesheet" href="https://fonts.googleapis.com/css2?family=Nunito+Sans:wght@400;600;700;800&display=swap">
<style>
  :root {
    --crimson: #c5203e;
    --ink: #1b1b1b;
    --paper: #ffffff;
    --stage: #2a2a2b;
    --text-grey: #4a4a4a;
    --rule: #d6d6d6;
  }
  * { box-sizing: border-box; margin: 0; padding: 0; }
  html, body { width: 1200px; height: 900px; overflow: hidden; }
  body {
    background: var(--stage);
    font-family: "Nunito Sans", "Avenir", sans-serif;
    display: flex;
    flex-direction: column;
    align-items: center;
    justify-content: center;
    gap: 44px;
  }
  .card {
    width: 620px;
    height: 360px;
    position: relative;
    overflow: hidden;
  }
  /* Back */
  .card-back {
    background: var(--ink);
    display: flex;
    align-items: center;
    justify-content: center;
  }
  .wordmark {
    display: flex;
    align-items: center;
    gap: 18px;
  }
  .wordmark-square {
    width: 48px;
    height: 48px;
    background: var(--crimson);
  }
  .wordmark-name {
    font-weight: 800;
    font-size: 25px;
    line-height: 1.02;
    letter-spacing: 0.5px;
    text-transform: uppercase;
  }
  .card-back .wordmark-name { color: var(--paper); }
  /* Front */
  .card-front {
    background: var(--paper);
    display: flex;
    align-items: center;
  }
  .accent-stripe {
    position: absolute;
    left: 0; top: 0; bottom: 0;
    width: 14px;
    background: var(--crimson);
  }
  .front-brand {
    width: 300px;
    padding-left: 62px;
  }
  .front-brand .wordmark-name { color: var(--ink); font-size: 21px; }
  .front-brand .wordmark-square { width: 40px; height: 40px; }
  .divider {
    width: 1px;
    height: 180px;
    background: var(--rule);
  }
  .contact {
    padding-left: 22px;
  }
  .contact-name {
    color: var(--crimson);
    font-weight: 800;
    font-size: 22px;
    line-height: 1.1;
  }
  .contact-role {
    color: var(--ink);
    font-weight: 700;
    font-size: 13px;
    margin-bottom: 16px;
  }
  .contact-address {
    color: var(--text-grey);
    font-size: 14px;
    line-height: 1.3;
    margin-bottom: 14px;
  }
  .contact-lines { list-style: none; }
  .contact-lines li {
    display: flex;
    align-items: center;
    gap: 10px;
    color: var(--text-grey);
    font-size: 14.5px;
    line-height: 1.45;
  }
  .contact-lines svg { width: 13px; height: 13px; flex: none; }
</style>
</head>
<body>
  <section class="card card-back" aria-label="Card back">
    <div class="wordmark">
      <span class="wordmark-square"></span>
      <span class="wordmark-name">Kelbrath<br>Baine<br>Tullock</span>
    </div>
  </section>

  <section class="card card-front" aria-label="Card front">
    <span class="accent-stripe"></span>
    <div class="front-brand">
      <div class="wordmark">
        <span class="wordmark-square"></span>
        <span class="wordmark-name">Kelbrath<br>Baine<br>Tullock</span>
      </div>
    </div>
    <span class="divider"></span>
    <div class="contact">
      <p class="contact-name">Doran Kelbrath</p>
      <p class="contact-role">Partner</p>
      <p class="contact-address">Level 3, 118 Wendmore Street<br>Sydney NSW 2000</p>
      <ul class="contact-lines">
        <li>
          <svg viewBox="0 0 12 16" aria-hidden="true"><rect x="1" y="0.8" width="10" height="14.4" rx="1.5" fill="none" stroke="#c5203e" stroke-width="1.6"/><circle cx="6" cy="12.5" r="0.9" fill="#c5203e"/></svg>
          0461 738 524
        </li>
        <li>
          <svg viewBox="0 0 16 12" aria-hidden="true"><rect x="0" y="0" width="16" height="12" rx="1" fill="#c5203e"/><path d="M1 1.2 L8 6.8 L15 1.2" fill="none" stroke="#ffffff" stroke-width="1.3"/></svg>
          doran@kbtlaw.co
        </li>
        <li>
          <svg viewBox="0 0 16 16" aria-hidden="true"><circle cx="8" cy="8" r="7.5" fill="#c5203e"/><ellipse cx="8" cy="8" rx="3" ry="7" fill="none" stroke="#ffffff" stroke-width="1"/><path d="M1 8 H15 M2.5 4.5 H13.5 M2.5 11.5 H13.5" stroke="#ffffff" stroke-width="1"/></svg>
          www.kbtlaw.co
        </li>
      </ul>
    </div>
  </section>
</body>
</html>
```